QZSTREAMHUB ( Wordpress website for catalogue of Vorlo Stream Pages)

Need a website to showcase different Vorlo Stream pages ( in different categories). Similar to e-commerce except no check-out / purchase of items. Pls use our logos provided and color scheme to be white+red+ blue as per our logo.

Target Market(s)

Consumers

Font styles to use
Sans Serif

Colors
ffffff
ec1f27
3276b5

Requirements
Must have
• I will need a Wordpress Theme as a handover. Also, pls use the color scheme (red+blue+white) as per logo attached. Prefer clean and near design with white space.

```html
<!DOCTYPE html>
<html lang="en">
<head>
<meta charset="utf-8">
<title>QZSTREAMHUB – A Portal of Curated Vorlo Stream</title>
<link rel="stylesheet" href="https://fonts.googleapis.com/css2?family=Roboto+Condensed:wght@300;400;700&family=Yellowtail&display=swap">
<style>
:root{
  --red:#ec1f27;
  --blue:#1f4fc4;
  --blue-soft:#3276b5;
  --ink:#1a1a1a;
  --grey:#555;
  --line:#8aa2d8;
  --white:#ffffff;
}
*{box-sizing:border-box;margin:0;padding:0}
html,body{width:1200px;height:3894px;overflow:hidden;background:var(--white)}
body{position:relative;font-family:"Roboto Condensed",Arial,sans-serif;color:var(--ink)}
.abs{position:absolute}

/* header */
.brand{position:absolute;left:133px;top:20px;font-weight:700;font-size:36px;color:var(--blue);letter-spacing:-0.5px}
.nav{position:absolute;top:21px;left:556px}
.nav a{position:absolute;top:0;height:36px;line-height:36px;font-size:21px;color:#333;text-decoration:none;white-space:nowrap}
.nav a.active{background:var(--blue);color:var(--white);border-radius:5px;padding:0 14px}

/* hero */
.hero-title{position:absolute;z-index:2;left:124px;top:196px;font-weight:700;font-size:66px;line-height:57px;letter-spacing:-2px;color:#111;white-space:nowrap}
.hero-title .of{font-family:"Yellowtail",cursive;font-weight:400;color:var(--red);font-size:60px;letter-spacing:0;margin-left:2px}
.hero-title .tag{display:inline-block;background:var(--red);color:var(--white);padding:2px 8px 0;margin-top:6px;line-height:54px;letter-spacing:0}
.hero-art{position:absolute;z-index:1;left:455px;top:128px;width:671px;height:318px;border-radius:60px 160px 20px 20px;
  background:linear-gradient(110deg,#eef2fb 0%,#dbe5fa 45%,#c9d7f7 70%,#f4d7da 100%)}
.stripe{position:absolute;left:0;top:473px;width:1200px;height:11px;background:linear-gradient(100deg,var(--red) 0 47%,var(--blue) 47.3% 100%)}

/* section titles */
.sec-title{position:absolute;font-weight:700;font-size:56px;line-height:64px;letter-spacing:-1px;white-space:nowrap}
.sec-title .b{color:var(--blue)}
.sec-title .r{display:inline-block;background:var(--red);color:var(--white);padding:0 10px;border-radius:4px;line-height:62px}
.sec-title .k{color:#111}

/* cards */
.card{position:absolute;width:266px;height:388px;background:var(--white);box-shadow:0 2px 10px rgba(0,0,0,.14)}
.card .media{height:165px;position:relative}
.card .live{position:absolute;left:18px;bottom:12px;background:rgba(236,31,39,.85);color:var(--white);font-weight:700;font-size:18px;padding:0 5px;line-height:22px}
.card h3{margin:26px 24px 0;font-size:20px;line-height:25px;font-weight:700}
.card p{margin:14px 24px 0;font-size:16px;line-height:21px;font-weight:300;color:var(--grey)}
.m1{background:linear-gradient(160deg,#3f5a5a,#1c2b22 60%,#2f5a2e)}
.m2{background:linear-gradient(160deg,#d9d2cf,#b8b0ad 60%,#e7c8c4)}
.m3{background:linear-gradient(160deg,#3a4dd0,#1a1f6b 55%,#0c0c1e)}
.m4{background:linear-gradient(160deg,#b58a8a,#7a5e63 55%,#d7a6c2)}
.m5{background:linear-gradient(160deg,#e9ebec,#9aa2a6 55%,#3b3f42)}
.m6{background:linear-gradient(160deg,#6ec2e4,#dbe6ee 50%,#f3f3f3)}

.btn{position:absolute;background:var(--red);color:var(--white);font-weight:700;text-align:center;border-radius:4px}

/* photos */
.photo{position:absolute;left:0;width:1200px}
.flame{top:1627px;height:420px;background:linear-gradient(90deg,#2b2c26 0%,#5c3a1e 30%,#e0611b 55%,#f09a3a 70%,#4a4a45 100%)}
.coffee{top:2632px;height:499px;background:linear-gradient(120deg,#3a2b22 0%,#8a6a4c 30%,#2a221d 55%,#6e5a4d 80%,#2b2522 100%)}

/* about */
.about-sub{position:absolute;left:171px;top:2190px;width:470px;color:var(--red);font-weight:700;font-size:29px;line-height:34px}
.about-text{position:absolute;left:171px;top:2282px;width:462px;font-size:17px;line-height:21.8px;font-weight:300;color:var(--grey)}

/* contact */
.contact-text{position:absolute;left:290px;top:3264px;width:620px;text-align:center;font-size:17px;line-height:22px;font-weight:300;color:var(--grey)}
.field{position:absolute;border:1.5px solid var(--line);border-radius:3px;background:var(--white);font-size:17px;color:#666;padding:0 16px;line-height:45px;font-weight:300}

/* footer */
.rule{position:absolute;left:0;top:3630px;width:1200px;height:1px;background:#ddd}
.foot-brand{position:absolute;left:0;width:1200px;top:3662px;text-align:center;font-weight:700;font-size:54px;color:var(--blue);letter-spacing:-0.5px}
.foot-nav a{position:absolute;top:3744px;font-size:21px;color:#333;text-decoration:none}
.copy{position:absolute;left:0;width:1200px;top:3788px;text-align:center;font-size:13px;color:#333}
.social{position:absolute;top:3829px;width:45px;height:40px;background:var(--red);border-radius:5px}
</style>
</head>
<body>

<header>
  <div class="brand">QZSTREAMHUB</div>
  <nav class="nav">
    <a class="active" style="left:0">Home</a>
    <a style="left:119px">About Us</a>
    <a style="left:252px">Stories</a>
    <a style="left:367px">News</a>
    <a style="left:470px">Conatct</a>
  </nav>
</header>

<section class="hero">
  <div class="hero-art" role="img" aria-label="Illustration of a phone showing a live stream beside two shoppers with bags, parcels, food and a clothes rack"></div>
  <h1 class="hero-title">A PORTAL<span class="of">of</span><br>CURATED<br>VORLO<br><span class="tag">STREAM</span></h1>
  <div class="stripe"></div>
</section>

<section class="stories">
  <h2 class="sec-title" style="left:0;width:1200px;text-align:center;top:557px"><span class="b">VORLO </span><span class="r">STREAM</span><span class="k"> STORIES</span></h2>

  <article class="card" style="left:171px;top:665px">
    <div class="media m1" role="img" aria-label="Photo of a footballer kicking a ball in a stadium"><span class="live">LIVE</span></div>
    <h3>Lorem ipsum dolor sitam et consectetur adipiscing elitsed do eiusmmpor</h3>
    <p>Lorem ipsum dolor sit amet, consectetur adipiscing elit, sed do eiusmod tempor incididunt ut labore et dolore ma</p>
  </article>
  <article class="card" style="left:466px;top:665px">
    <div class="media m2" role="img" aria-label="Photo of a plush eared headband with a flower"><span class="live">LIVE</span></div>
    <h3>Lorem ipsum dolor sitam et consectetur adipiscing elitsed do eiusmmpor</h3>
    <p>Lorem ipsum dolor sit amet, consectetur adipiscing elit, sed do eiusmod tempor incididunt ut labore et dolore ma</p>
  </article>
  <article class="card" style="left:760px;top:665px">
    <div class="media m3" role="img" aria-label="Photo of a concert crowd under stage lights"><span class="live">LIVE</span></div>
    <h3>Lorem ipsum dolor sitam et consectetur adipiscing elitsed do eiusmmpor</h3>
    <p>Lorem ipsum dolor sit amet, consectetur adipiscing elit, sed do eiusmod tempor incididunt ut labore et dolore ma</p>
  </article>

  <article class="card" style="left:171px;top:1085px">
    <div class="media m4" role="img" aria-label="Photo of a pink plush headband held up"><span class="live">LIVE</span></div>
    <h3>Lorem ipsum dolor sitam et consectetur adipiscing elitsed do eiusmmpor</h3>
    <p>Lorem ipsum dolor sit amet, consectetur adipiscing elit, sed do eiusmod tempor incididunt ut labore et dolore ma</p>
  </article>
  <article class="card" style="left:466px;top:1085px">
    <div class="media m5" role="img" aria-label="Photo of chefs cooking in a restaurant kitchen"><span class="live">LIVE</span></div>
    <h3>Lorem ipsum dolor sitam et consectetur adipiscing elitsed do eiusmmpor</h3>
    <p>Lorem ipsum dolor sit amet, consectetur adipiscing elit, sed do eiusmod tempor incididunt ut labore et dolore ma</p>
  </article>
  <article class="card" style="left:760px;top:1085px">
    <div class="media m6" role="img" aria-label="Photo of a fluffy blue and white plush toy"><span class="live">LIVE</span></div>
    <h3>Lorem ipsum dolor sitam et consectetur adipiscing elitsed do eiusmmpor</h3>
    <p>Lorem ipsum dolor sit amet, consectetur adipiscing elit, sed do eiusmod tempor incididunt ut labore et dolore ma</p>
  </article>

  <a class="btn" style="left:490px;top:1520px;width:220px;height:61px;line-height:61px;font-size:21px">VIEW ALL STORIES</a>
</section>

<div class="photo flame" role="img" aria-label="Photo of a flaming pan held over a stove"></div>

<section class="about">
  <h2 class="sec-title" style="left:171px;top:2122px"><span class="b">ABOUT </span><span class="r">US</span></h2>
  <p class="about-sub">Lorem ipsum dolor sitamet consetetur adipiscing elitsed do eiusmm</p>
  <p class="about-text">Sed ut perspiciatis unde omnis iste natus error sit voluptatem acc usantium doloremque laudantium, totam rem aperiam, eaque ipsa quae ab illo inventore veritatis et quasi architecto beatae vitae dicta sunt explicabo. Nemo enim ipsam voluptatem quia voluptas sit asp ernatur aut odit aut fugit, sed quia consequuntur magni dolores eos qui ratione voluptatem sequi nesciunt. Neque porro quisquam est, qui dolorem ipsum quia dolor sit amet, consectetur, adipisci velit, sed quia non numquam eius modi tempora incidunt ut labore et dolore magnam aliquam quaerat voluptatem.</p>
  <a class="btn" style="left:171px;top:2489px;width:149px;height:53px;line-height:53px;font-size:20px">READ MORE</a>

  <svg class="abs" style="left:680px;top:2130px" width="420" height="420" viewBox="0 0 420 420">
    <circle cx="60" cy="76" r="53" fill="#f2b6c0"/>
    <circle cx="317" cy="288" r="98" fill="#b9cff5"/>
  </svg>
  <div class="abs" style="left:681px;top:2142px;width:384px;height:384px;border-radius:50%;background:linear-gradient(135deg,#c8242a 0%,#e24b3d 30%,#8fb04a 50%,#d9d04a 65%,#e0862c 85%,#c0262e 100%)" role="img" aria-label="Collage of fresh fruit: tomatoes, grapes, packaged produce and oranges"></div>
</section>

<div class="photo coffee" role="img" aria-label="Photo of an espresso machine pouring coffee into a cup"></div>

<section class="contact">
  <h2 class="sec-title" style="left:0;width:1200px;text-align:center;top:3186px"><span class="b">CONTACT </span><span class="r">US</span></h2>
  <p class="contact-text">usantium doloremque laudantium, totam rem aperiam, eaque ipsa quae ab illo inventore veritatis et quasi architecto beatae vitae dicta sunt explicabo enim ipsam voluptatem</p>
  <div class="field" style="left:275px;top:3336px;width:284px;height:48px">Name</div>
  <div class="field" style="left:275px;top:3397px;width:284px;height:48px">Email</div>
  <div class="field" style="left:275px;top:3457px;width:284px;height:48px">Phone</div>
  <div class="field" style="left:275px;top:3516px;width:284px;height:48px">Subject</div>
  <div class="field" style="left:568px;top:3336px;width:284px;height:168px">Message</div>
  <a class="btn" style="left:568px;top:3516px;width:284px;height:48px;line-height:48px;font-size:19px">SUBMIT</a>
</section>

<footer>
  <div class="rule"></div>
  <div class="foot-brand">QZSTREAMHUB</div>
  <nav class="foot-nav">
    <a style="left:364px">Home</a>
    <a style="left:455px">About Us</a>
    <a style="left:573px">Stories</a>
    <a style="left:678px">News</a>
    <a style="left:766px">Conatct</a>
  </nav>
  <p class="copy">© 2020 QZSTREAMHUB. All rights reserved.</p>
  <a class="social" style="left:524px" aria-label="Social link"></a>
  <a class="social" style="left:577px" aria-label="Social link"></a>
  <a class="social" style="left:630px" aria-label="Social link"></a>
</footer>

</body>
</html>
```